Brevlon Website Design - Wordpress

Need a website WordPress design for our existing website that we just stood up. The logo is already in place and name. Brevlon.example We are a company which makes connections with our clients through educating them and providing networking events. We would like for the website to show a VIP/special feel to it.

Target Market(s)

Business executives and employees. Age group 26-65 in the following sectors:
- Technology
- Human Resources
- Finance
- Sales

Industry/Entity Type

Technical Service

Number of Pages Required

4 page

Font styles to use
Sans Serif

Requirements
Must have
• Must be something for Wordpress
Nice to have
• Would like this to be professional but look cutting edge and VIP.

```html
<!DOCTYPE html>
<html lang="en">
<head>
<meta charset="utf-8">
<title>Brevlon — Expand Your Business</title>
<link href="https://fonts.googleapis.com/css2?family=Lato:wght@400;700&family=Montserrat:wght@400;500;600;800&display=swap" rel="stylesheet">
<style>
:root{
  --red:#c1272d;
  --red-dark:#a81f24;
  --green:#3a9b3a;
  --gold:#d9a11b;
  --purple:#5c2b80;
  --blue:#1f5aa6;
  --ink:#111111;
  --dark:#0c0c0d;
  --text:#444444;
  --white:#ffffff;
  --head:'Montserrat',Arial,sans-serif;
  --body:'Lato',Arial,sans-serif;
}
*{margin:0;padding:0;box-sizing:border-box}
html,body{width:1200px;height:3965px;overflow:hidden}
body{font-family:var(--body);background:var(--white);color:var(--text);position:relative}
section,header,footer{position:absolute;left:0;width:1200px;overflow:hidden}
.abs{position:absolute}
.btn{position:absolute;display:flex;align-items:center;justify-content:center;font-family:var(--head);font-weight:600;font-size:12px;letter-spacing:.5px;color:var(--white);text-transform:uppercase}

/* hero */
.hero{top:0;height:642px;background:#1a222b}
.hero-photo{position:absolute;inset:0;background:linear-gradient(100deg,#dfe3e6 0%,#8d98a1 25%,#4b5863 50%,#2a3440 75%,#161c24 100%)}
.hero-shade{position:absolute;inset:0;background:linear-gradient(180deg,rgba(0,0,0,.55) 0%,rgba(0,0,0,.1) 30%,rgba(0,0,0,.25) 100%)}
.brand{position:absolute;left:172px;top:26px;display:flex;align-items:center;gap:12px}
.brand-mark{width:18px;height:18px;background:var(--white)}
.brand-name{font-family:var(--head);font-weight:500;font-size:26px;letter-spacing:3px;color:var(--white)}
.nav{position:absolute;top:36px;left:660px;display:flex;gap:48px;font-family:var(--head);font-size:15px;color:var(--white)}
.hero-title{position:absolute;left:172px;top:238px;font-family:var(--head);font-weight:800;font-size:50px;line-height:62px;color:var(--white)}

/* welcome */
.welcome{top:642px;height:566px;background:var(--white)}
.welcome-photo{position:absolute;left:0;top:0;width:600px;height:566px;background:linear-gradient(135deg,#b9a89a 0%,#d8d3cf 35%,#8a98a6 65%,#c7ccd1 100%);clip-path:polygon(0 0,520px 0,585px 566px,0 566px)}
.section-heading{font-family:var(--head);font-weight:500;font-size:31px;color:var(--ink)}
.accent-gold{color:var(--gold)}
.accent-red{color:var(--red)}
.para{font-size:12.5px;line-height:22px;color:var(--text)}

/* strategy */
.strategy{top:1208px;height:655px;background:radial-gradient(ellipse at 50% 60%,#1a1a1c 0%,var(--dark) 70%)}
.dark-title{position:absolute;left:0;width:1200px;text-align:center;font-family:var(--head);font-weight:500;font-size:26px;color:var(--white)}
.dark-sub{position:absolute;left:0;width:1200px;text-align:center;font-size:13px;line-height:21px;color:#6d6d6d}
.trait{position:absolute;font-family:var(--head);color:var(--white);font-size:16px}
.trait small{display:block;font-family:var(--body);font-size:11px;color:#666;margin-top:2px}

/* offer */
.offer{top:1863px;height:648px;background:linear-gradient(180deg,#0a0a0a 0%,#151517 50%,#0a0a0a 100%)}
.offer-item{position:absolute;width:230px;text-align:center}
.offer-item svg{display:block;margin:0 auto}
.offer-label{font-family:var(--head);font-size:14px;margin-top:12px;text-transform:uppercase}
.offer-desc{font-size:12px;line-height:20px;color:#9a9a9a;margin-top:14px;padding:0 18px}
.offer-box{position:absolute;left:378px;top:207px;width:217px;height:267px;border:1.5px solid var(--gold)}

/* networking */
.networking{top:2511px;height:507px;background:var(--white)}
.net-photo{position:absolute;inset:0;background:linear-gradient(120deg,#d9dde1 0%,#9aa3ad 45%,#56626e 75%,#2a3946 100%);clip-path:polygon(760px 0,1200px 0,1200px 507px,640px 507px)}

/* meetup */
.meetup{top:3018px;height:590px;background:linear-gradient(180deg,#111 0%,#0b0b0b 100%)}
.tile{position:absolute;width:291px;height:172px;overflow:hidden}
.tile-photo{position:absolute;inset:0}
.tile-flag{position:absolute;left:0;top:0;width:150px;height:110px}
.tile-date{position:absolute;left:12px;top:12px;font-family:var(--head);font-size:15px;color:var(--white)}

/* footer */
.site-footer{top:3615px;height:350px}
.footer-bg{position:absolute;inset:0;background:linear-gradient(100deg,#6a2e74 0%,#7a4a6a 30%,#9a7a3a 60%,var(--green) 90%)}
.footer-head{position:absolute;font-family:var(--head);font-weight:500;font-size:14px;letter-spacing:.5px;color:var(--white)}
.footer-text{position:absolute;font-size:11.5px;line-height:19px;color:var(--white)}
.footer-links{position:absolute;list-style:none;font-size:11.5px;line-height:24px;color:var(--white)}
.social{position:absolute;left:176px;top:306px;display:flex;gap:12px}
.social span{width:28px;height:28px;border:1.5px solid var(--white);border-radius:50%}
</style>
</head>
<body>

<header class="hero">
  <div class="hero-photo" role="img" aria-label="Business team in a meeting around a table with laptops"></div>
  <div class="hero-shade"></div>
  <div class="brand"><span class="brand-mark"></span><span class="brand-name">BREVLON</span></div>
  <nav class="nav"><span>Events</span><span>Expand</span><span>X</span><span>About</span><span>Connect</span></nav>
  <h1 class="hero-title">EXPAND<br>YOUR BUSINESS</h1>
</header>

<section class="welcome">
  <div class="welcome-photo" role="img" aria-label="Colleagues working on laptops and a tablet in an office"></div>
  <h2 class="section-heading abs" style="left:580px;top:122px">Welcome to <span class="accent-gold">&nbsp;BREVLON</span></h2>
  <p class="para abs" style="left:580px;top:180px;width:450px">At vero eos et accusamus et iusto odio dignissimos ducimus qui blanditiis praesentium voluptatum deleniti atque corrupti quos dolores et quas molestias excepturi sint occaecati cupiditate non provident, similique sunt in culpa qui officia deserunt mollitia animi, id est laborum et dolorum fuga. Et harum quidem rerum facilis est et expedita distinctio. Nam libero tempore, cum soluta nobis est eligendi optio cumque nihil impedit quo minus id quod maxime placeat facere possimus, omnis voluptas assumenda est, omnis dolor repellendus. Temporibus autem quibusdam et aut officiis rerum necessitatibus saepe eveniet ut et voluptates repudiandae sint et mo</p>
  <span class="btn" style="left:580px;top:391px;width:108px;height:34px;background:var(--red-dark)">Read more</span>
</section>

<section class="strategy">
  <h2 class="dark-title" style="top:80px">It's about our unique X Strategy</h2>
  <p class="dark-sub" style="top:126px">BREVLON provides impactful connection opportunities to help<br>educate, equip and expand you and your business</p>
  <svg class="abs" style="left:0;top:0" width="1200" height="655" viewBox="0 0 1200 655">
    <g fill="none" stroke="#2b2b2b" stroke-width="1.5">
      <circle cx="600" cy="378" r="200"/>
      <circle cx="600" cy="378" r="160" stroke="#1f1f1f"/>
    </g>
    <g stroke-width="1.2" fill="none">
      <polyline points="365,238 440,238 470,268" stroke="var(--blue)"/>
      <polyline points="835,238 760,238 730,268" stroke="var(--red)"/>
      <polyline points="365,545 440,545 470,515" stroke="var(--purple)"/>
      <polyline points="835,545 760,545 730,515" stroke="var(--gold)"/>
    </g>
    <g fill="var(--green)">
      <circle cx="600" cy="240" r="3.5"/><circle cx="600" cy="516" r="3.5"/>
      <circle cx="462" cy="378" r="3.5"/><circle cx="738" cy="378" r="3.5"/>
      <circle cx="440" cy="238" r="3"/><circle cx="760" cy="238" r="3"/>
      <circle cx="440" cy="545" r="3"/><circle cx="760" cy="545" r="3"/>
    </g>
    <circle cx="600" cy="378" r="110" fill="#141415" stroke="#2e2e2e"/>
    <text x="600" y="386" text-anchor="middle" font-family="Montserrat, Arial, sans-serif" font-size="24" letter-spacing="3" fill="#ffffff">BREVLON</text>
    <g stroke="var(--blue)" stroke-width="1.6" fill="none">
      <circle cx="332" cy="238" r="18"/><path d="M322 238h20M332 228v20M324 230l16 16M340 230l-16 16"/>
    </g>
    <path d="M862 252 l-17-16 a9 9 0 0 1 17-11 a9 9 0 0 1 17 11 z" fill="none" stroke="var(--red)" stroke-width="1.8"/>
    <g stroke="var(--purple)" stroke-width="1.6" fill="none">
      <path d="M322 555 v-20 a4 4 0 0 1 8 0 v10 M344 555 v-20 a4 4 0 0 0 -8 0 v10"/><circle cx="333" cy="526" r="5"/>
    </g>
    <g stroke="var(--gold)" stroke-width="1.6" fill="none">
      <rect x="842" y="540" width="7" height="15"/><rect x="853" y="532" width="7" height="23"/><rect x="864" y="524" width="7" height="31"/><path d="M838 558h38"/>
    </g>
  </svg>
  <div class="trait" style="left:306px;top:270px">Mind<small>Strategy</small></div>
  <div class="trait" style="left:842px;top:270px">Heart<small>Passion</small></div>
  <div class="trait" style="left:313px;top:474px">Soul<small>Purpose</small></div>
  <div class="trait" style="left:842px;top:466px">Strength<small>Energy</small></div>
</section>

<section class="offer">
  <h2 class="dark-title" style="top:94px">What we offer you</h2>
  <div class="offer-box"></div>
  <div class="offer-item" style="left:139px;top:225px">
    <svg width="64" height="58" viewBox="0 0 64 58" fill="none" stroke="var(--green)" stroke-width="2"><path d="M6 8h22a4 4 0 0 1 4 4v40a4 4 0 0 0-4-4H6z"/><path d="M58 8H36a4 4 0 0 0-4 4v40a4 4 0 0 1 4-4h22z"/><path d="M12 18h14M12 26h14M12 34h14M38 18h14M38 26h14M38 34h14"/></svg>
    <div class="offer-label" style="color:var(--green)">Educate</div>
    <p class="offer-desc">At BREVLON, we provide effective training and learning as the foundation for building a healthy, successful company</p>
  </div>
  <div class="offer-item" style="left:371px;top:225px">
    <svg width="64" height="58" viewBox="0 0 64 58" fill="none" stroke="var(--gold)" stroke-width="2"><circle cx="32" cy="22" r="16"/><circle cx="32" cy="22" r="7"/><path d="M24 40h16M26 46h12M28 52h8M32 2v4M48 6l-3 3M16 6l3 3"/></svg>
    <div class="offer-label" style="color:var(--gold)">Equip</div>
    <p class="offer-desc">Through our connected eco system of companies, we'll help find the right partners for equipping you to move forward.</p>
  </div>
  <div class="offer-item" style="left:593px;top:225px">
    <svg width="64" height="58" viewBox="0 0 64 58" fill="none" stroke="var(--red)" stroke-width="2"><path d="M4 16h14l24 26h16M4 42h14l24-26h16M52 10l6 6-6 6M52 36l6 6-6 6"/></svg>
    <div class="offer-label" style="color:var(--red)">Exchange</div>
    <p class="offer-desc">We connect you with others who have successfully implemented our X Strategy to facilitate growth in their business</p>
  </div>
  <div class="offer-item" style="left:823px;top:225px">
    <svg width="64" height="58" viewBox="0 0 64 58" fill="none" stroke="#7a3aa8" stroke-width="2"><rect x="8" y="4" width="50" height="50"/><path d="M22 40 44 18M30 18h14v14"/></svg>
    <div class="offer-label" style="color:#7a3aa8">Expand</div>
    <p class="offer-desc">Our goal is to help you and your business increase productivity and scale through effective strategy and healthy culture.</p>
  </div>
  <span class="btn" style="left:527px;top:542px;width:146px;height:44px;background:var(--red-dark);font-size:13px">X = Value</span>
</section>

<section class="networking">
  <div class="net-photo" role="img" aria-label="Hands joining colourful puzzle pieces together"></div>
  <h2 class="section-heading abs" style="left:172px;top:106px;font-size:30px">Networking <span class="accent-red">Events</span></h2>
  <p class="para abs" style="left:172px;top:162px;width:440px">At vero eos et accusamus et iusto odio dignissimos ducimus qui blanditiis praesentium voluptatum deleniti atque corrupti quos dolores et quas molestias excepturi sint occaecati cupiditate non provident, similique sunt in culpa qui officia deserunt mollitia animi, id est laborum et dolorum fuga. Et harum quidem rerum facilis est et expedita distinctio. Nam libero tempore, cum soluta nobis est eligendi optio cumque nihil impedit quo minus id quod maxime placeat facere possimus, omnis voluptas assumenda est, omnis dolor repellendus. Temporibus autem quibusdam et aut officiis rerum necessitatibus saepe eveniet ut et voluptates repudiandae sint et mo</p>
  <span class="btn" style="left:172px;top:372px;width:108px;height:34px;background:var(--purple)">Read more</span>
</section>

<section class="meetup">
  <h2 class="section-heading abs" style="left:172px;top:150px;font-size:26px;color:var(--white)">Meetup</h2>
  <p class="abs" style="left:172px;top:206px;width:205px;font-size:12px;line-height:20px;color:#8a8a8a">At vero eos et accusamus et iusto odio dignissimos ducimus qui blanditiis praesentium voluptatum deleniti atque corrupti quos dolores et quas molestias excepturi sint occaecati cupiditate non provident, similique sunt in culpa qui officia deserunt mollitia animi, id est laborum et dolorum fuga.</p>
  <span class="btn" style="left:172px;top:398px;width:108px;height:34px;background:var(--green)">Connect</span>

  <div class="tile" style="left:431px;top:114px">
    <div class="tile-photo" role="img" aria-label="Professionals at a meetup table with laptops" style="background:linear-gradient(135deg,#7aa6c9,#c9b8a6 60%,#4a5866)"></div>
    <svg class="tile-flag" viewBox="0 0 150 110"><polygon points="0,0 150,0 0,110" fill="var(--blue)" opacity=".9"/></svg>
    <span class="tile-date">Mar 05</span>
  </div>
  <div class="tile" style="left:735px;top:114px">
    <div class="tile-photo" role="img" aria-label="Businessman presenting at a glass window" style="background:linear-gradient(135deg,#9aa5ae,#d7dbde 55%,#2d3640)"></div>
    <svg class="tile-flag" viewBox="0 0 150 110"><polygon points="0,0 150,0 0,110" fill="var(--red)" opacity=".9"/></svg>
    <span class="tile-date">Mar 16</span>
  </div>
  <div class="tile" style="left:431px;top:304px">
    <div class="tile-photo" role="img" aria-label="Two colleagues reviewing documents together" style="background:linear-gradient(135deg,#8e8a86,#cfc7bd 50%,#3b3f47)"></div>
    <svg class="tile-flag" viewBox="0 0 150 110"><polygon points="0,0 150,0 0,110" fill="var(--purple)" opacity=".9"/></svg>
    <span class="tile-date">Mar 09</span>
  </div>
  <div class="tile" style="left:735px;top:304px">
    <div class="tile-photo" role="img" aria-label="Two executives in conversation" style="background:linear-gradient(135deg,#b9c3cc,#e3e6e8 50%,#2f3a48)"></div>
    <svg class="tile-flag" viewBox="0 0 150 110"><polygon points="0,0 150,0 0,110" fill="var(--gold)" opacity=".9"/></svg>
    <span class="tile-date">Mar 15</span>
  </div>
</section>

<footer class="site-footer">
  <div class="footer-bg" role="img" aria-label="Decorative colour background in purple, gold and green"></div>
  <div class="brand" style="top:78px"><span class="brand-mark"></span><span class="brand-name">BREVLON</span></div>
  <p class="footer-text" style="left:172px;top:150px;font-family:var(--head);font-weight:600;font-size:13px;line-height:22px">Phone: 1-855-555-0142<br>Email: connect@brevlon.example</p>

  <div class="footer-head" style="left:415px;top:66px">ABOUT US</div>
  <p class="footer-text" style="left:415px;top:100px;width:180px">Modo phasera blandit faucibus arcu turpis, scelerisque in nisl sapien blandit sem. Cras quis dui vitae justo maximum tincidunt ut ut adipiscing vel nisl etiam blandit varius quis dui vitae justo maximum sollicitudin.</p>

  <div class="footer-head" style="left:682px;top:66px">NEWSLETTER</div>
  <p class="footer-text" style="left:682px;top:100px;width:170px">Subscribe to us to get and receive the latest news, sales and updates.</p>
  <div class="footer-text" style="left:682px;top:186px;width:165px;border-bottom:1px solid rgba(255,255,255,.6);padding-bottom:4px;font-size:11px">Email Address</div>
  <span class="btn" style="left:682px;top:228px;width:100px;height:32px;border-radius:16px;background:var(--red-dark)">Sign up</span>

  <div class="footer-head" style="left:909px;top:66px">LINKS</div>
  <ul class="footer-links" style="left:909px;top:100px">
    <li>Sed ut perspiciatis</li><li>Unde omnis iste natus</li><li>Voluptatem accusan</li><li>Totam doloremque</li><li>Haudatnium</li><li>Totm doloremque</li>
  </ul>

  <div class="abs" style="left:172px;top:290px;width:856px;height:1px;background:rgba(255,255,255,.45)"></div>
  <div class="social"><span></span><span></span><span></span><span></span></div>
  <p class="footer-text" style="left:698px;top:312px;font-size:11px">© 2019 BREVLON. All rights reserved. Privacy | Terms of use</p>
</footer>

</body>
</html>
```